Tradlo - Forex Signal Services Moments Matter Most. Reshape your path.

I need an attractive eye catching web design that is azure friendly. I currently have a web programmer working on the backend of my website. Now I need a professional design to attract and retain customers. This site needs to be mobile friendly.

Tradlo is a highly reputable, trustworthy and professional site that offers forex signals to traders in all parts of the globe. With accurate and reliable forex signals, traders can not only make money but also boost their profits.

At Tradlo, we want our clients to have complete faith on us and our services! We also do not want our users to lead a simple and monotonous life. Instead our goal is to help them create an extra source of steady income. However, this is possible only when our clients resolve to change their lives for the better. They need to change their mindset and most importantly develop a positive frame of mind. That’s exactly why at Tradlo, we provide our clients with innumerable personal development tools and resources that’ll aid them in changing all the aspects of their lives. We want our traders to feel inspired and educate them in the right way!

Colors are flexible.

I do like the simplicity of www.brightmarkvo.example.
I do want a design more professional in appearance and not everything on page one.

I have not been able to decide on a logo. There is one of lower quality as I have not paid for it yet but I will if you decide it's the best for my business I will. Or should one feel that they have a better idea for a logo, I will pay for it if i like it.

I have included some of the content of my site so you can get a feel for where I am coming from.
(Please note that this content is still in the editing process)
Updates

Project Deadline Extended Reason: My content was not complete nor finalization of the final logo. We will allow a few more days for designers to modify the website.Thank you for your patience and understanding. Added Tuesday, January 24, 2017

Target Market(s)

I work with Forex Traders, Investors wanting to control their own portfolios, and remote nomads/mellienials

Coding

Coded - Design and coding required

Number of Pages Required

5+ page

Requirements
Must have
• I must have a professional clean look. I want the site to be interactive and eye catching. I want my audience hooked within seconds of opening it. It has to have all important information first. Photos must be legit and not spammy. I work as a representative in the financial market. I want my site to reflect that I stand by my product and reputation means everything to me. This site has to be engaging.
• Sorry, I should have included this earlier of what I will all need on this site.
• I'll have about Tradlo (my company, what we stand for, who we work with, my strategy, etc....
• about me (why i started this company, who I am)
• Performance (graphs and recent posts of signals)
• Membership (how to sign up)
• Terms of service/legal/disclaimers
• FAQS
• Personal Development Resources
• Forex Education Resources
Nice to have
• Quick links to bounce around the site faster.
Should not have
• I do not want over the top white collar conservative.

```html
<!DOCTYPE html>
<html lang="en">
<head>
<meta charset="utf-8">
<title>Tradlo - Forex Signal Services</title>
<link rel="stylesheet" href="https://fonts.googleapis.com/css2?family=Open+Sans:wght@400;600&family=Roboto:wght@400;500&display=swap">
<style>
:root{
  --red:#b3181d;
  --ink:#222;
  --text:#555;
  --muted:#777;
  --line:#ddd;
  --white:#fff;
  --footer:#4a4a4a;
  --sans:"Open Sans",Arial,sans-serif;
  --ui:"Roboto",Arial,sans-serif;
}
*{box-sizing:border-box;margin:0;padding:0}
html,body{width:1200px;height:2782px;overflow:hidden;background:var(--white);font-family:var(--sans);color:var(--text)}
.page{position:relative;width:1200px;height:2782px}
section,header,footer{position:absolute;left:0;width:1200px}

.site-header{top:0;height:126px;border-top:3px solid var(--red);background:var(--white)}
.brand{position:absolute;left:124px;top:34px;display:flex;align-items:center;gap:10px;font-family:var(--sans);font-weight:600;font-size:30px;color:var(--ink)}
.brand-dot{width:22px;height:22px;border-radius:50%;background:var(--red)}
.search{position:absolute;left:1040px;top:28px}
.nav{position:absolute;left:508px;top:84px;font-family:var(--ui);font-size:12px;letter-spacing:.5px;color:#444}
.nav a{color:inherit;text-decoration:none;position:absolute;height:42px;white-space:nowrap}
.nav .n1{left:0}
.nav .n2{left:96px}
.nav .n3{left:218px}
.nav .n4{left:372px}
.nav .n5{left:484px}
.nav .active{color:var(--red)}
.nav .active::after{content:"";position:absolute;left:-8px;right:-8px;top:36px;height:3px;background:var(--red)}

.hero{top:126px;height:464px;background:linear-gradient(135deg,#2a0f0c 0%,#5a2a10 30%,#1b2230 60%,#3a1a08 100%);text-align:center;color:var(--white)}
.hero-title{position:absolute;top:156px;width:100%;font-size:37px;font-weight:400;letter-spacing:.5px}
.hero-sub{position:absolute;top:226px;width:100%;font-size:21px}
.btn-red{display:inline-block;background:var(--red);color:var(--white);font-family:var(--sans);text-decoration:none;border-radius:3px}
.hero .btn-red{position:absolute;left:497px;top:286px;width:204px;height:52px;line-height:52px;font-size:21px}
.dots{position:absolute;top:416px;left:0;width:100%;display:flex;justify-content:center;gap:8px}
.dots span{width:7px;height:7px;border-radius:50%;background:rgba(255,255,255,.5)}
.dots span:first-child{background:var(--white)}

.welcome{top:590px;height:269px;text-align:center}
.welcome h1{position:absolute;top:60px;width:100%;font-size:40px;font-weight:600;color:var(--ink)}
.welcome p{position:absolute;left:130px;top:134px;width:940px;font-size:11.5px;line-height:24px;color:var(--muted)}

.band{color:var(--white);text-align:center}
.band h2{position:absolute;top:66px;width:100%;font-size:36px;font-weight:400}
.band p{position:absolute;left:128px;width:944px;font-size:11.5px;line-height:24px}
.btn-ghost{position:absolute;left:497px;width:204px;height:52px;line-height:48px;border:2px solid var(--white);border-radius:3px;color:var(--white);text-decoration:none;font-size:20px}
.strategy{top:859px;height:415px;background:linear-gradient(120deg,#1c2838 0%,#2f3f55 35%,#151c28 70%,#3a4656 100%)}
.strategy p{top:150px}
.strategy .btn-ghost{top:265px}
.why-tradlo{top:1786px;height:390px;background:linear-gradient(120deg,#1a2e6a 0%,#3b2a6a 40%,#6a1f2a 75%,#2a1a3a 100%)}
.why-tradlo h2{top:62px}
.why-tradlo p{top:140px}
.why-tradlo .btn-ghost{top:253px}

.why-us{top:1274px;height:512px}
.why-us h2{position:absolute;left:132px;top:76px;font-size:37px;font-weight:400;color:var(--ink)}
.why-us .intro{position:absolute;left:132px;top:138px;width:470px;font-size:12px;line-height:24px;color:var(--muted)}
.ticks{position:absolute;left:132px;top:208px;list-style:none;font-size:15px;color:#333}
.ticks li{display:flex;align-items:center;gap:18px;height:29.5px}
.why-us .btn-red{position:absolute;left:130px;top:353px;width:124px;height:43px;line-height:43px;text-align:center;font-size:14px}
.video{position:absolute;left:612px;top:106px;width:455px;height:286px;border:3px solid #e5e5e5;background:radial-gradient(ellipse at 45% 55%,#2ba9d8 0%,#0c4f7a 40%,#061a2c 100%)}

.contact{top:2176px;height:388px}
.contact h3{position:absolute;left:132px;top:70px;font-family:var(--ui);font-size:15px;font-weight:500;color:#222;letter-spacing:.3px}
.field{position:absolute;border:1px solid var(--line);border-radius:3px;font-family:var(--ui);font-size:11px;color:#666;padding:14px 12px}
.f-name{left:132px;top:130px;width:282px;height:42px}
.f-email{left:428px;top:130px;width:282px;height:42px}
.f-msg{left:132px;top:189px;width:578px;height:85px}
.contact .btn-red{position:absolute;left:132px;top:297px;width:104px;height:37px;line-height:37px;text-align:center;font-family:var(--ui);font-size:14px}
.info{position:absolute;left:744px;top:128px;list-style:none;font-family:var(--ui);font-size:11px;color:#666}
.info li{display:flex;gap:14px;height:27px;align-items:flex-start}
.info svg{flex:none;margin-top:1px}
.info .addr{line-height:18px;margin-top:-4px}

.site-footer{top:2564px;height:218px;background:var(--footer);color:#ddd;font-size:10px}
.site-footer .copy{position:absolute;left:132px;top:28px}
.site-footer .legal{position:absolute;left:132px;top:62px;width:940px;line-height:20px}
</style>
</head>
<body>
<div class="page">
  <header class="site-header">
    <div class="brand"><span class="brand-dot"></span>Tradlo</div>
    <svg class="search" width="24" height="24" viewBox="0 0 24 24" fill="none" stroke="#444" stroke-width="1.6"><circle cx="10" cy="10" r="8"/><path d="M16 16l7 7"/></svg>
    <nav class="nav">
      <a class="n1 active" href="#">HOME</a>
      <a class="n2" href="#">ABOUT US</a>
      <a class="n3" href="#">OUR STRATEGY</a>
      <a class="n4" href="#">WHY US?</a>
      <a class="n5" href="#">CONTACT US</a>
    </nav>
  </header>

  <section class="hero" role="img" aria-label="Close-up of a trading screen with currency rates and charts">
    <h1 class="hero-title">MOMENTS MATTER MOST. RESHAPE YOUR PATH</h1>
    <p class="hero-sub">We use proven strategies to help traders in succeeding in the forex market.</p>
    <a class="btn-red" href="#">Start Free Trial</a>
    <div class="dots"><span></span><span></span><span></span></div>
  </section>

  <section class="welcome">
    <h1>WELCOME TO TRADLO.EXAMPLE!</h1>
    <p>We use proven strategies to help traders in succeeding in the forex market. Our forex experts provide high-probability, professional and consistent forex signals and charts that help traders in maximizing their profits and eliminating losses. Try our free Currency Education service to find out what differentiates us from our competitors and how we can aid you in becoming a professional trader!</p>
  </section>

  <section class="band strategy" role="img" aria-label="Currency board showing exchange rates">
    <h2>OUR STRATEGY</h2>
    <p>Tradlo works with both day as well as intraday traders. We only hold a maximum of one position at any given point in time. Once we've placed an order we do not move SL or TP targets. We follow naked forex trading techniques including price action, immediate trend and personalized mathematical formulas. Our success stems from our strict enforcement of discipline, patience, attitude, economics and timing to help our traders maximize their gains from forex trading.</p>
    <a class="btn-ghost" href="#">Learn More</a>
  </section>

  <section class="why-us">
    <h2>WHY US?</h2>
    <p class="intro">Put simply, because we're different! We are a 'Never before Seen' forex trading-company that is focused on guiding.</p>
    <ul class="ticks">
      <li><svg width="12" height="12" viewBox="0 0 12 12"><circle cx="6" cy="6" r="6" fill="var(--red)"/><path d="M5 3.5L7.5 6 5 8.5" stroke="#fff" stroke-width="1.4" fill="none"/></svg>We offer speedy, consistent, accurate and desired results.</li>
      <li><svg width="12" height="12" viewBox="0 0 12 12"><circle cx="6" cy="6" r="6" fill="var(--red)"/><path d="M5 3.5L7.5 6 5 8.5" stroke="#fff" stroke-width="1.4" fill="none"/></svg>We're a highly dependable</li>
      <li><svg width="12" height="12" viewBox="0 0 12 12"><circle cx="6" cy="6" r="6" fill="var(--red)"/><path d="M5 3.5L7.5 6 5 8.5" stroke="#fff" stroke-width="1.4" fill="none"/></svg>Our motto is to 'Reshape Your Path'</li>
      <li><svg width="12" height="12" viewBox="0 0 12 12"><circle cx="6" cy="6" r="6" fill="var(--red)"/><path d="M5 3.5L7.5 6 5 8.5" stroke="#fff" stroke-width="1.4" fill="none"/></svg>Our objective is to provide global access</li>
    </ul>
    <a class="btn-red" href="#">Learn More</a>
    <div class="video" role="img" aria-label="Video preview of a glowing world map with market data"></div>
  </section>

  <section class="band why-tradlo" role="img" aria-label="Blurred city lights and trading board at night">
    <h2>WHY TRADLO</h2>
    <p>We're a small company based in the beautiful mountains, Pinecrest, Northvale with over 9 years of successful trading experience in the foreign exchange market. We decided to launch our service for two reasons: learning to trade is a difficult process that leaves many aspiring traders frustrated, and on top of that, there is no shortage of bad signal services that take advantage of these traders. Our aim is to help aspiring traders become profitable while they're learning to trade, and even if they do not have the time</p>
    <a class="btn-ghost" href="#">Learn More</a>
  </section>

  <section class="contact">
    <h3>IF YOU HAVE ANY QUESTIONS PLEASE SEND US AN EMAIL AND WE'LL GET BACK TO YOU PROMPTLY.</h3>
    <div class="field f-name">Name</div>
    <div class="field f-email">Email</div>
    <div class="field f-msg">Message</div>
    <a class="btn-red" href="#">SUBMIT</a>
    <ul class="info">
      <li><svg width="13" height="13" viewBox="0 0 13 13" fill="#777"><path d="M3 1h2l1 3-1.5 1a7 7 0 003.5 3.5L9 7l3 1v2a2 2 0 01-2 2A9 9 0 011 3a2 2 0 012-2z"/></svg>(555) 014-2290</li>
      <li><svg width="13" height="13" viewBox="0 0 13 13" fill="#777"><rect x="3" y="1" width="7" height="3"/><rect x="1" y="5" width="11" height="5" rx="1"/><rect x="3" y="8" width="7" height="4" fill="#fff" stroke="#777"/></svg>(555) 014-2290</li>
      <li><svg width="13" height="13" viewBox="0 0 13 13" fill="none" stroke="#777" stroke-width="1.3"><rect x="1" y="2.5" width="11" height="8"/><path d="M1 3l5.5 4L12 3"/></svg><u>info@tradlo.example</u></li>
      <li><svg width="13" height="13" viewBox="0 0 13 13" fill="#777"><path d="M6.5 0A4.5 4.5 0 002 4.5C2 8 6.5 13 6.5 13S11 8 11 4.5A4.5 4.5 0 006.5 0zm0 6.3a1.8 1.8 0 110-3.6 1.8 1.8 0 010 3.6z"/></svg><span class="addr">#2868 Lorem ipsum dolor sit amet,<br>consectetur</span></li>
    </ul>
  </section>

  <footer class="site-footer">
    <p class="copy">© tradlo.example 2017 | All rights reserved</p>
    <p class="legal">Disclaimer Trading foreign exchange ("Forex") on margin carries a high level of risk, and may not be suitable for all investors. Before deciding to trade Forex you should carefully consider your investment objectives, level of experience, and only trade with the money you are prepared to lose. The possibility exists that you could sustain a loss in excess of all of your deposited funds and therefore you should not speculate with capital that you cannot afford to lose. You should be aware of all the risks associated with foreign exchange. Clients must be at least 18 years old to use the services of TRADLO. You acknowledge that past performance is not an indicator of future returns and that references to performance on this Site are provided as historical benchmarks only. TRADLO does not take responsibility for loss incurred as a result of our trading signals. By signing up as a member you acknowledge that we are not providing financial advice and that you are making the decision to use our trades on your own account. All information provided by TRADLO, in any form, is for educational purposes only.</p>
  </footer>
</div>
</body>
</html>
```